Business Card for premium dental clinic

We are a premium dental clinic based in Brasov, Romania with more than 15 year on the market, providing quality dental treatment made by a team of more specialized dentists, working with modern equipment as a solution to beautiful and healthy teeth.

Our current logo for the clinic use 2 square with colors black and gold - dr Ternisu - studio, using family fonts Bodoni, Myriad Pro and Segoe Print.
Depending on the printing we used some gold CMYK background or gold foil picture background or a gold gradient.
We want a business card:
- eye catching business card
- distinguished business card
- premium design
- to keep the color scheme of black and gold
- to attract the customers to spent time reading the information
- modern concept

```html
<!DOCTYPE html>
<html lang="en">
<head>
<meta charset="UTF-8">
<title>dr Ternisu – Business Card</title>
<link href="https://fonts.googleapis.com/css2?family=Lato:wght@400;700&family=Oswald:wght@500&display=swap" rel="stylesheet">
<style>
  :root {
    --bg: #e4e4e6;
    --black: #0d0d0d;
    --white: #ffffff;
    --gold: #b98a2c;
    --ink: #1c1c1c;
    --grey: #6b6b6b;
    --faint: #ededed;
    --shadow: 0 14px 30px rgba(0,0,0,0.18);
  }
  * { box-sizing: border-box; margin: 0; padding: 0; }
  html, body { width: 1200px; height: 900px; overflow: hidden; }
  body {
    background: var(--bg);
    font-family: "Lato", Arial, sans-serif;
    color: var(--ink);
    position: relative;
  }
  .card {
    position: absolute;
    border-radius: 24px;
    overflow: hidden;
    box-shadow: var(--shadow);
    background: var(--white);
  }

  /* Appointment side */
  .card-appointment { left: 70px; top: 80px; width: 560px; height: 320px; display: flex; flex-direction: column; }
  .band { background: var(--black); color: var(--white); display: flex; align-items: center; justify-content: center; }
  .band-top { height: 78px; font-size: 24px; font-weight: 700; letter-spacing: 0.3px; }
  .band-bottom { height: 82px; margin-top: auto; font-size: 17px; font-weight: 700; }
  .appointment-fields { padding: 34px 40px 0; font-size: 16px; color: var(--grey); }
  .field-row { display: flex; align-items: flex-end; gap: 8px; }
  .dots { flex: 1; border-bottom: 2px dotted #999; height: 1px; margin-bottom: 5px; }
  .ampm { margin-left: 4px; }
  .days { display: flex; justify-content: space-between; margin-top: 30px; }
  .day { display: flex; align-items: center; gap: 6px; font-size: 15px; }
  .box { width: 20px; height: 20px; border: 1.5px solid #777; }

  /* Contact side */
  .card-contact { left: 540px; top: 470px; width: 600px; height: 340px; }
  .name-faint {
    position: absolute; right: 36px; top: 26px;
    font-family: "Lato", Arial, sans-serif; font-weight: 700;
    font-size: 58px; color: var(--faint); letter-spacing: 1px;
  }
  .brand-name {
    position: absolute; left: 40px; top: 104px;
    font-size: 34px; font-weight: 700; color: var(--black);
  }
  .address {
    position: absolute; right: 40px; top: 150px; text-align: right;
    font-size: 15px; line-height: 1.35; color: var(--ink); font-style: normal;
  }
  .person { position: absolute; left: 40px; top: 178px; }
  .person-name { font-family: "Oswald", Arial, sans-serif; font-weight: 500; font-size: 24px; color: var(--gold); line-height: 1; }
  .person-role { font-size: 16px; margin-top: 3px; }
  .contacts { list-style: none; margin-top: 12px; font-size: 17px; line-height: 1.45; }
  .contacts li { display: flex; align-items: center; gap: 10px; }
  .contacts svg { width: 14px; height: 14px; fill: var(--gold); flex: none; }
</style>
</head>
<body>

  <section class="card card-appointment">
    <div class="band band-top">Your Next Appointment on</div>
    <div class="appointment-fields">
      <div class="field-row">
        <span>Date :</span><span class="dots"></span>
        <span>Time :</span><span class="dots"></span>
        <span class="ampm">AM / PM</span>
      </div>
      <div class="days">
        <span class="day"><span class="box"></span>MON</span>
        <span class="day"><span class="box"></span>TUE</span>
        <span class="day"><span class="box"></span>WED</span>
        <span class="day"><span class="box"></span>THU</span>
        <span class="day"><span class="box"></span>FRI</span>
        <span class="day"><span class="box"></span>SAT</span>
      </div>
    </div>
    <div class="band band-bottom">If unable to keep appointment, kindly give 24hrs notice.</div>
  </section>

  <section class="card card-contact">
    <div class="name-faint" aria-hidden="true">dr Ternisu</div>
    <div class="brand-name">dr Ternisu</div>
    <address class="address">
      18, Strada Lunga<br>Brasov, 500035
    </address>
    <div class="person">
      <div class="person-name">Andrei Morolan</div>
      <div class="person-role">Managing Director</div>
      <ul class="contacts">
        <li><svg viewBox="0 0 16 16"><path d="M3 1l3 1 1 4-2 1a9 9 0 004 4l1-2 4 1 1 3-2 2C7 15 1 9 1 3z"/></svg>044-987 650 321</li>
        <li><svg viewBox="0 0 16 16"><path d="M1 3h14v10H1z M2 4l6 5 6-5" stroke="#fff" stroke-width="1.2"/></svg>hello@ternisu.ro</li>
        <li><svg viewBox="0 0 16 16"><circle cx="8" cy="8" r="7"/></svg>www.ternisu.ro</li>
      </ul>
    </div>
  </section>

</body>
</html>
```